Redesign of LumoWordfind.com in Bootstrap 4

Current design of LumoWordfind.com is not responsive. We need to change it to latest version of Bootstrap 4 keeping essential elements in place.

Apart from home page, we need designs for http://www.lumowordfind.com/meaning/cat also.

Coding

Number of Pages Required

2 page

Colors
34a7d8

Requirements
Must have
• Bootstrap 4

```html
<!DOCTYPE html>
<html lang="en">
<head>
<meta charset="utf-8">
<title>Lumo Wordfind</title>
<link href="https://fonts.googleapis.com/css2?family=Roboto:wght@400;500;700&family=Open+Sans:wght@400;600&display=swap" rel="stylesheet">
<style>
:root{
  --blue:#34a7d8;
  --orange:#f39c12;
  --dark:#2e2e2e;
  --footer:#333333;
  --footer-bottom:#2a2a2a;
  --text:#666;
  --tile:#4a4a4a;
  --white:#fff;
}
*{margin:0;padding:0;box-sizing:border-box}
html,body{width:869px;height:1200px;overflow:hidden;background:#fff}
body{position:relative;font-family:"Open Sans",sans-serif;color:var(--text)}
.abs{position:absolute}
.heading{font-family:"Roboto",sans-serif}

/* top bar */
.topbar{top:0;left:0;width:869px;height:42px;background:#fff;font-size:9.5px;color:#444}
.topbar .contact{left:72px;top:14px;display:flex;gap:10px;align-items:center}
.topbar .contact span{display:flex;align-items:center;gap:5px}
.topbar .social{left:628px;top:15px;display:flex;gap:9px}
.topbar .social i{display:block;width:10px;height:10px;border-radius:2px;background:#888}
.topbar .search{left:694px;top:9px;width:104px;height:24px;border:1px solid #e2e2e2;font-size:8px;color:#aaa;padding:6px 6px}

/* nav */
.nav{top:42px;left:0;width:869px;height:63px;background:linear-gradient(#3fb0e0,#2b9bcd)}
.nav .brandbox{left:0;top:0;width:171px;height:63px;background:linear-gradient(#fdfdfd,#dcdcdc)}
.brand{left:76px;top:15px;width:90px;z-index:2;font-family:"Roboto",sans-serif;font-weight:700;font-size:14px;line-height:16px;color:var(--blue);display:flex;align-items:center;gap:6px}
.brand b{display:block;flex:none;width:9px;height:9px;border-radius:50%;background:var(--orange)}
.nav ul{list-style:none;left:195px;top:26px;display:flex;gap:33px;font-family:"Roboto",sans-serif;font-weight:500;font-size:9.5px;color:#fff;text-transform:uppercase}
.nav ul li.active{position:relative}
.nav ul li.active:after{content:"";position:absolute;left:2px;right:2px;top:17px;height:2px;background:#fff}
.btn{top:19px;height:26px;font-family:"Roboto",sans-serif;font-weight:500;font-size:10px;color:#fff;display:flex;align-items:center;justify-content:center;border-radius:2px}
.btn-login{left:655px;width:66px;background:var(--orange)}
.btn-register{left:732px;width:66px;background:#4a4a4a}

/* hero */
.hero{top:105px;left:0;width:869px;height:405px;background:var(--dark);overflow:hidden}
.hero svg{position:absolute;left:0;top:0}
.hero h1{left:72px;top:42px;font-size:17px;font-weight:700;color:#fff;letter-spacing:.2px}
.hero .field{left:72px;top:80px;width:242px;height:29px;border:1px solid #666;font-size:9.5px;color:#ddd;padding:8px 9px}
.hero .go{left:314px;top:80px;width:71px;height:29px;background:var(--orange);color:#fff;font-family:"Roboto",sans-serif;font-weight:700;font-size:12px;display:flex;align-items:center;justify-content:center}
.hero .rule{left:72px;top:137px;width:326px;height:1px;background:#444}
.hero h2{left:72px;top:165px;font-size:16px;font-weight:700;color:var(--blue)}
.hero ul{left:72px;top:200px;list-style:none;font-size:10px;color:#e6e6e6}
.hero li{height:28.6px;display:flex;gap:7px}
.hero li svg{position:static;margin-top:2px}
.dots{left:72px;top:361px;display:flex;gap:5px}
.dots i{width:9px;height:9px;border:2px solid #fff;border-radius:50%}
.dots i.on{border-color:var(--blue)}

/* welcome */
.welcome{top:510px;left:0;width:869px;height:150px;text-align:center}
.welcome h2{margin-top:32px;font-size:18px;font-weight:700;color:var(--blue)}
.welcome p{margin:16px auto 0;width:700px;font-size:7.6px;line-height:17.5px;color:#888}

/* services */
.services{top:660px;left:0;width:869px;height:322px;background:linear-gradient(#eef0f1,#f6f7f7);text-align:center}
.services h2{margin-top:22px;font-size:18px;font-weight:700;color:var(--blue)}
.services .lead{margin-top:14px;font-size:8.8px;color:#555}
.tile{width:90px;height:90px;background:var(--tile);display:flex;align-items:center;justify-content:center}
.tile.active{background:var(--blue)}
.svc{top:102px;width:160px;display:flex;flex-direction:column;align-items:center}
.svc h3{margin-top:14px;font-family:"Roboto",sans-serif;font-weight:400;font-size:10.5px;color:#333;text-transform:uppercase}
.svc h3.hl{color:var(--blue)}
.svc p{margin-top:5px;font-size:8px;line-height:16px;color:#666}
.svc a{color:#444}

/* browse */
.browse{top:1011px;left:72px;width:726px;height:37px;background:#fff;box-shadow:0 2px 5px rgba(0,0,0,.15);display:flex;align-items:center;padding-left:11px}
.browse strong{font-family:"Roboto",sans-serif;font-size:9.5px;color:var(--blue);width:147px}
.browse .letters{display:flex;justify-content:space-between;width:556px;font-size:10.5px;color:#555}
.browse .letters span:first-child{color:var(--blue)}

/* footer */
.footer{top:1072px;left:0;width:869px;height:93px;background:var(--footer);font-size:8.5px;color:#fff}
.col{top:22px;line-height:15px}
.col h4{font-weight:400;font-size:8.5px;color:var(--blue)}
.fbrand{left:521px;top:30px;font-family:"Roboto",sans-serif;font-weight:700;font-size:14px;line-height:16px;color:#777}
.follow{left:643px;top:34px;display:flex;align-items:center;gap:7px;font-size:7px;color:var(--blue)}
.follow i{display:block;width:20px;height:20px;border-radius:50%;background:#fff}
.copy{top:1165px;left:0;width:869px;height:35px;background:var(--footer-bottom);font-size:8px;color:#fff;text-align:center;line-height:35px}
</style>
</head>
<body>

<header class="topbar abs">
  <div class="contact abs">
    <span><svg width="9" height="9" viewBox="0 0 10 10"><path d="M2 1l2 2-1 1.5a6 6 0 003 3L7.5 6l2 2-1.5 1.5C4 9.5.5 6 .5 2.5z" fill="#34a7d8"/></svg>Call Us Now : 555-010-4477</span>
    <span><svg width="10" height="8" viewBox="0 0 10 8"><rect x=".5" y=".5" width="9" height="7" fill="none" stroke="#34a7d8"/><path d="M.5 .5l4.5 4 4.5-4" fill="none" stroke="#34a7d8"/></svg>info@lumowordfind.com</span>
  </div>
  <div class="social abs"><i></i><i></i><i></i></div>
  <div class="search abs">Search</div>
</header>

<nav class="nav abs">
  <div class="brandbox abs"></div>
  <div class="brand abs"><b></b><span>Lumo<br>Wordfind</span></div>
  <ul class="abs">
    <li class="active">Home</li><li>Idioms</li><li>Common Errors</li><li>Crossword</li><li>Blog</li><li>Contact</li>
  </ul>
  <div class="btn btn-login abs">LOG IN</div>
  <div class="btn btn-register abs">REGISTER</div>
</nav>

<section class="hero abs">
  <svg width="869" height="405" viewBox="0 0 869 405">
    <path d="M490 0 Q300 200 478 405 L869 405 L869 0Z" fill="#f39c12"/>
    <path d="M508 0 Q316 200 488 405 L869 405 L869 0Z" fill="#34a7d8"/>
    <defs><linearGradient id="photoTone" x1="0" y1="0" x2="1" y2="1"><stop offset="0" stop-color="#d9d6d0"/><stop offset=".5" stop-color="#bdb9b2"/><stop offset="1" stop-color="#8f8a82"/></linearGradient></defs>
    <path d="M520 0 Q330 200 500 405 L869 405 L869 0Z" fill="url(#photoTone)" role="img" aria-label="Photo of a magnifying glass resting on an open book"/>
  </svg>
  <h1 class="abs heading">LUMO ENGLISH WORDFIND !</h1>
  <div class="field abs">Enter a word or phrase</div>
  <div class="go abs">Search</div>
  <div class="rule abs"></div>
  <h2 class="abs heading">SEARCH, SAVE AND MASTER WORDS</h2>
  <ul class="abs">
    <li><svg width="9" height="8" viewBox="0 0 9 8"><path d="M1 4l2.5 2.5L8 1" fill="none" stroke="#34a7d8" stroke-width="2"/></svg>Search from more than 300,000 words and phrases</li>
    <li><svg width="9" height="8" viewBox="0 0 9 8"><path d="M1 4l2.5 2.5L8 1" fill="none" stroke="#fff" stroke-width="2"/></svg>Multiple usages to clarify the context</li>
    <li><svg width="9" height="8" viewBox="0 0 9 8"><path d="M1 4l2.5 2.5L8 1" fill="none" stroke="#fff" stroke-width="2"/></svg>Audio, phonetics, meanings, synonyms and antonyms</li>
    <li><svg width="9" height="8" viewBox="0 0 9 8"><path d="M1 4l2.5 2.5L8 1" fill="none" stroke="#fff" stroke-width="2"/></svg>Save the words to your personal deck and access from anywhere</li>
    <li><svg width="9" height="8" viewBox="0 0 9 8"><path d="M1 4l2.5 2.5L8 1" fill="none" stroke="#fff" stroke-width="2"/></svg>It's FREE</li>
  </ul>
  <div class="dots abs"><i></i><i class="on"></i><i></i><i></i></div>
</section>

<section class="welcome abs">
  <h2 class="heading">WELCOME TO OUR COMPANY</h2>
  <p>Lorem Ipsum es simplemente el texto de relleno de las imprentas y archivos de texto. Lorem Ipsum ha sido el texto de relleno estándar de las industrias desde el año 1500, cuando un impresor (N. del T. persona que se dedica a la imprenta) desconocido usó una galería de textos y los mezcló de tal manera que logró hacer un libro de textos especimen. No sólo sobrevivió 500 años, sino que tambien ingresó como texto</p>
</section>

<section class="services abs">
  <h2 class="heading">OUR SERVICES</h2>
  <p class="lead">Es simplemente el texto de relleno de las imprentas y archivos de texto. Lorem Ipsum ha sido el texto de relleno estándar de las...</p>

  <div class="svc abs" style="left:65px">
    <div class="tile active"><svg width="34" height="34" viewBox="0 0 34 34" fill="none" stroke="#fff" stroke-width="3" stroke-linecap="round"><path d="M14 10l-5 5a4 4 0 006 6"/><path d="M20 24l5-5a4 4 0 00-6-6"/><path d="M6 6l3 3M28 28l-3-3M4 14h3M30 20h-3"/></svg></div>
    <h3 class="hl">English Tidbit</h3>
    <p>Gaffe" is a social blunder and "gaff" is a large hook. Be warned not the gaffe of mixing it up with gaff.</p>
  </div>
  <div class="svc abs" style="left:259px">
    <div class="tile"><svg width="34" height="34" viewBox="0 0 34 34" fill="none" stroke="#fff" stroke-width="2.5"><path d="M6 22V4h10l5 5v4"/><path d="M13 13h10l5 5v13H13z"/></svg></div>
    <h3>Daily Crossword</h3>
    <p>ake this daily crossword challenge<br>from Lumo Wordfind.<br><a href="#">Salve Now</a></p>
  </div>
  <div class="svc abs" style="left:453px">
    <div class="tile"><svg width="34" height="34" viewBox="0 0 34 34"><circle cx="17" cy="17" r="14" fill="#fff"/></svg></div>
    <h3>Browser Addon</h3>
    <p>Add this tool to your Browser and quickly look up for definitions website without leaving the page.</p>
  </div>
  <div class="svc abs" style="left:646px">
    <div class="tile"><svg width="22" height="36" viewBox="0 0 22 36" fill="none" stroke="#fff" stroke-width="2.5"><rect x="2" y="2" width="18" height="32" rx="3"/><path d="M2 8h18M2 27h18"/><circle cx="11" cy="30.5" r="1" fill="#fff"/></svg></div>
    <h3>Designed for Phone</h3>
    <p>Lumo Wordfind is specially designed for your Phone to quickly lookup meaining.</p>
  </div>
</section>

<div class="browse abs">
  <strong>BROWSE DICTIONARY :</strong>
  <div class="letters"><span>A</span><span>B</span><span>C</span><span>D</span><span>E</span><span>F</span><span>G</span><span>H</span><span>I</span><span>J</span><span>K</span><span>L</span><span>M</span><span>N</span><span>O</span><span>P</span><span>Q</span><span>R</span><span>S</span><span>T</span><span>U</span><span>V</span><span>W</span><span>X</span><span>Y</span><span>Z</span></div>
</div>

<footer class="footer abs">
  <div class="col abs" style="left:72px"><h4>LUMOWORDFIND.COM</h4><div>FAQ</div><div>Contact</div><div>Blog</div></div>
  <div class="col abs" style="left:221px"><h4>LEGAL</h4><div>Privacy Policy</div><div>Terms of Use</div></div>
  <div class="col abs" style="left:339px"><h4>OTHERS</h4><div>Popular Words</div><div>Common Errors in English</div><div>Exam Prep Online</div></div>
  <div class="fbrand abs">Lumo<br>Wordfind</div>
  <div class="follow abs">FOLLOW US :<i></i><i></i><i></i><i></i></div>
</footer>
<div class="copy abs">Copyright. 2016.Lumo Wordfind All rights reserved.</div>

</body>
</html>
```